Fjordlys buisnesscard

Hey :) I need a modern buisnesscard for my company Fjordlys
It most have:
Dagligleder og Fotograf: Henrik Audun Strandvik

Mob: +4791264085
Epost: post@fjordlys.example
Adresse: Kvernbakken9, 6040 Havnevik

Facbook and instagram logo with text Fjordlys

Fjordlys logo

It Company

```html
<!DOCTYPE html>
<html lang="no">
<head>
<meta charset="utf-8">
<title>Fjordlys – visittkort</title>
<link rel="stylesheet" href="https://fonts.googleapis.com/css2?family=Open+Sans:wght@400;600;700;800&display=swap">
<style>
  :root {
    --stage: #ece8e1;
    --card: #ffffff;
    --brand-blue: #2f8bc0;
    --brand-blue-deep: #2579ab;
    --brand-pink: #d2387f;
    --text-light: #eaf4fb;
    --rule: #9cc8e2;
    --shadow: rgba(40, 30, 20, 0.22);
  }
  * { box-sizing: border-box; margin: 0; padding: 0; }
  html, body {
    width: 1200px; height: 950px; overflow: hidden;
    background: var(--stage);
    font-family: "Open Sans", Arial, sans-serif;
  }
  .stage {
    width: 1200px; height: 950px;
    display: flex; justify-content: center; align-items: center; gap: 80px;
  }
  .card {
    position: relative;
    width: 440px; height: 770px;
    background: var(--card);
    box-shadow: 0 14px 30px var(--shadow);
    overflow: hidden;
  }

  /* Front side */
  .card-front__panel {
    position: absolute; left: 0; top: 0; right: 0; height: 470px;
    background: linear-gradient(160deg, var(--brand-blue) 0%, var(--brand-blue-deep) 100%);
    color: var(--text-light);
    padding: 80px 48px 0;
  }
  .holder-name {
    font-size: 24px; font-weight: 700; color: #fff; line-height: 1.2; white-space: nowrap;
  }
  .holder-role {
    margin-top: 6px; font-size: 17px; font-weight: 400;
  }
  .address {
    margin-top: 60px; font-size: 16px; line-height: 1.6; font-style: normal;
  }
  .contact-list {
    list-style: none; margin-top: 20px; font-size: 16px;
  }
  .contact-list li {
    display: flex; align-items: center; gap: 12px; line-height: 2;
  }
  .contact-list svg { width: 16px; height: 16px; flex: none; }
  .card-front__brand {
    position: absolute; left: 0; right: 0; top: 470px; bottom: 0;
    display: flex; align-items: center; justify-content: center;
  }
  .brand-name {
    font-weight: 800; color: var(--brand-blue); letter-spacing: 0.5px;
  }
  .card-front__brand .brand-name { font-size: 62px; }

  /* Back side */
  .card-back__logo {
    position: absolute; left: 110px; right: 30px; top: 0; bottom: 0;
    display: flex; align-items: center; justify-content: center; gap: 14px;
  }
  .card-back__logo .brand-name { font-size: 50px; }
  .logo-dot {
    width: 28px; height: 28px; border-radius: 50%; background: var(--brand-pink); flex: none;
  }
  .social-rail {
    position: absolute; left: 50px; top: 280px; height: 210px; width: 30px;
    display: flex; flex-direction: column; align-items: center; justify-content: center; gap: 14px;
  }
  .social-rail::before, .social-rail::after {
    content: ""; width: 1px; flex: 1; background: var(--rule);
  }
  .social-badge {
    width: 26px; height: 26px; border-radius: 50%;
    border: 1.5px solid var(--brand-blue);
  }
</style>
</head>
<body>
<main class="stage">
  <section class="card card-front" aria-label="Visittkort forside">
    <div class="card-front__panel">
      <h1 class="holder-name">Henrik Audun Strandvik</h1>
      <p class="holder-role">Dagligleder og Fotograf</p>
      <address class="address">Kvernbakken9<br>6040 Havnevik</address>
      <ul class="contact-list">
        <li>
          <svg viewBox="0 0 16 16" aria-hidden="true"><rect x="4" y="1" width="8" height="14" rx="1.5" fill="none" stroke="#fff" stroke-width="1.5"/><circle cx="8" cy="12.5" r="0.9" fill="#fff"/></svg>
          +4791264085
        </li>
        <li>
          <svg viewBox="0 0 16 16" aria-hidden="true"><rect x="1" y="3" width="14" height="10" rx="1" fill="#fff"/><path d="M1.5 3.5 8 9l6.5-5.5" fill="none" stroke="#2f8bc0" stroke-width="1.3"/></svg>
          post@fjordlys.example
        </li>
        <li>
          <svg viewBox="0 0 16 16" aria-hidden="true"><circle cx="8" cy="8" r="7" fill="#fff"/><path d="M1.5 8h13M8 1c-3 3.5-3 10.5 0 14M8 1c3 3.5 3 10.5 0 14" fill="none" stroke="#2f8bc0" stroke-width="1"/></svg>
          www.fjordlys.example
        </li>
      </ul>
    </div>
    <div class="card-front__brand">
      <span class="brand-name">Fjordlys</span>
    </div>
  </section>

  <section class="card card-back" aria-label="Visittkort bakside">
    <div class="social-rail" aria-label="Sosiale medier">
      <span class="social-badge"></span>
      <span class="social-badge"></span>
    </div>
    <div class="card-back__logo">
      <span class="logo-dot" aria-hidden="true"></span>
      <span class="brand-name">Fjordlys</span>
    </div>
  </section>
</main>
</body>
</html>
```